International professional tennis coach needs a book cover design

This is my 2nd published book, the first one was a #1 on the best seller. I'm looking for a world class book cover design for this new book. The name of my first book was 5 Baseline Habits to Unlock Your Flow Rhythm, located on Bookvale.com

The title of the new book:

Title: The Craft of Rally Mastery
Subtitle: Building a Tactical Edge through Smarter Match Insight

I'm uploading our new CRAFT OF RALLY logo that I'd like for you to use as the centerpiece of the book design along with a 21st century design feel that incorporates what the book topic is below::

--> This book is about building competitive intelligence by using tennis data analytics to develop and expand a player's strategic advantage for match play. <--

The colors we would like to use are Blue, Yellow, and Green. These shades of these colors should be bold! (You will see the bold color examples of blues, yellows, and greens that I'm talking about in the logos that are attached here, especially the colors for my Racket GridDrill App logo.

I will upload the Racket GridDrill logo which should go somewhere on the back cover design (small size maybe in the bottom corner).

This book is revolutionary to the standard way of teaching tennis, it is based on a decade of recording and gathering tennis data analytics and then we created on-court practice games to develop better decision making in players for the competitive edge.

My websites are www.elevatedrillzone.com and www.craftofrallymastery.com

```html
<!DOCTYPE html>
<html lang="en">
<head>
<meta charset="utf-8">
<title>The Craft of Rally Mastery — Book Cover</title>
<link rel="stylesheet" href="https://fonts.googleapis.com/css2?family=Oswald:wght@200;300;500;600;700&family=Montserrat:wght@300;400;600&display=swap">
<style>
  :root{
    --green-dark:#2a7a24;
    --green-mid:#4a9a3a;
    --green-light:#9acd5a;
    --blue:#1b82c9;
    --yellow:#f6c21c;
    --ink:#2b2b2b;
    --paper:#ffffff;
    --stage:#eeeeee;
  }
  *{box-sizing:border-box;margin:0;padding:0}
  html,body{width:1200px;height:924px;overflow:hidden;background:var(--stage)}
  .wrap{position:absolute;left:18px;top:42px;width:1164px;height:840px;display:flex;background:var(--paper);box-shadow:0 4px 18px rgba(0,0,0,.12)}
  .back{width:560px;height:840px;padding:52px 38px 30px;position:relative}
  .spine{width:44px;height:840px;border-left:1px solid #e4e4e4;border-right:1px solid #e4e4e4;position:relative}
  .front{width:560px;height:840px;padding:62px 50px 0;position:relative;text-align:center}

  /* back cover */
  .back-title{text-align:center;font-family:'Oswald',sans-serif;font-size:34px;letter-spacing:-.5px;line-height:1;margin-bottom:34px}
  .back-title .thin{font-weight:200;color:var(--green-dark)}
  .back-title .bold-light{font-weight:700;color:var(--green-light)}
  .back-title .bold-dark{font-weight:700;color:var(--green-mid)}
  .blurb p{font-family:'Montserrat',sans-serif;font-weight:300;font-size:9.6px;line-height:1.5;color:var(--ink);text-align:justify;margin-bottom:5px}
  .rule{height:1px;width:250px;margin:14px auto 12px;background:linear-gradient(90deg,transparent,var(--green-light),transparent)}
  .author-name{font-family:'Montserrat',sans-serif;font-weight:600;font-size:25px;color:var(--green-dark);text-align:center;margin-bottom:10px}
  .author{display:flex;gap:12px;align-items:flex-start}
  .author-photo{width:86px;height:108px;flex:none;background:linear-gradient(160deg,#8a9aa6,#3c4750)}
  .author-photo.outdoor{background:linear-gradient(160deg,#7fb0d9,#5d7a52)}
  .author p{font-family:'Montserrat',sans-serif;font-weight:400;font-size:9.6px;line-height:1.32;color:var(--ink);text-align:justify}
  .app-mark{position:absolute;left:40px;bottom:44px;display:flex;align-items:center;gap:6px;font-family:'Montserrat',sans-serif;font-weight:600;font-size:10px;color:var(--blue)}
  .app-mark .dot{width:16px;height:16px;border-radius:50%;background:var(--blue)}
  .code-box{position:absolute;right:38px;bottom:30px;width:138px;height:90px;border:1.5px solid var(--green-light)}

  /* spine */
  .spine-text{position:absolute;left:50%;top:24px;transform:translateX(-50%);writing-mode:vertical-rl;font-family:'Oswald',sans-serif;font-size:19px;line-height:1;white-space:nowrap}
  .spine-text .thin{font-weight:200;color:var(--green-dark)}
  .spine-text .bold-light{font-weight:700;color:var(--green-light)}
  .spine-text .bold-dark{font-weight:700;color:var(--green-dark)}
  .spine-dot{position:absolute;left:50%;top:344px;transform:translateX(-50%);width:18px;height:18px;border-radius:50%;background:var(--blue)}
  .spine-authors{position:absolute;left:50%;bottom:28px;transform:translateX(-50%);writing-mode:vertical-rl;font-family:'Oswald',sans-serif;font-weight:500;font-size:15px;color:var(--green-dark);white-space:nowrap}

  /* front cover */
  .title{font-family:'Oswald',sans-serif;line-height:.9;letter-spacing:-2px}
  .title .line-thin{display:block;font-weight:200;font-size:96px;color:var(--green-dark)}
  .title .line-light{display:block;font-weight:700;font-size:128px;color:var(--green-light)}
  .title .line-dark{display:block;font-weight:700;font-size:128px;color:var(--green-dark)}
  .brand-mark{height:200px;margin-top:30px;display:flex;align-items:center;justify-content:center;gap:12px;font-family:'Oswald',sans-serif;font-weight:700;font-size:34px;color:var(--blue);letter-spacing:1px}
  .brand-mark .dot{width:30px;height:30px;border-radius:50%;background:var(--blue)}
  .subtitle{margin:18px auto 0;width:430px;padding:10px 0;border-top:1px solid var(--green-light);border-bottom:1px solid var(--green-light);font-family:'Montserrat',sans-serif;font-weight:400;font-size:21px;line-height:1.3;color:var(--ink);letter-spacing:.5px}
  .byline{position:absolute;left:0;right:0;bottom:48px;font-family:'Oswald',sans-serif;font-weight:600;font-size:34px;color:var(--green-dark);letter-spacing:-.5px}
</style>
</head>
<body>
<main class="wrap">
  <section class="back">
    <h2 class="back-title"><span class="thin">THE CRAFT OF </span><span class="bold-light">RALLY </span><span class="bold-dark">MASTERY</span></h2>
    <div class="blurb">
      <p>A practical guide on how to win more matches by becoming a more efficient and effective competitor.</p>
      <p>As a tennis player you have the ability to play better matches and win more of them. The Craft of Rally Mastery gives you a system to improve. We start with the individual game of the set itself. Our system examines your physical and mental progression, enabling you to upgrade your movement and performance from shot to shot and point to point. Our system seamlessly integrates the technical (physical) aspects with the tactical (mental/emotional) components, providing a comprehensive approach to elevate this performance. We aim to give you much more than how to hit great shots. Irrespective of your current skill level, we will provide you with a detailed strategic and tactical plan to enhance your performance, leading to improved results and increased success in your matches.</p>
      <p>The Craft of Rally Mastery emphasizes the importance of shifting focus from oneself to the opponent, encouraging players to analyze and understand their adversaries. By bringing the opponent back to the forefront of their thinking, the player creates the best possible context in which to improve as a competitor. In this book, we present a groundbreaking approach to tennis data analytics that seamlessly integrates match performance with practice sessions, and vice versa.</p>
    </div>
    <div class="rule"></div>
    <h3 class="author-name">CORWIN HALLOWAY</h3>
    <div class="author">
      <div class="author-photo" role="img" aria-label="Portrait photo of Corwin Halloway on court"></div>
      <p>Corwin Halloway is regarded as one of the leading strategy and tactical coaches in the world today. He is the Creator of Racket GridDrill, the world's first Tennis Tracking App that maps and charts match play based on the rally length of a point. Corwin is a Best Selling Author of the book "5 Baseline Habits to Unlock Your Flow Rhythm" and the Co-Founder of The Craft of Rally Mastery promoting coach, player, and parent development. He is often sought after by coaches around the world to design the practice court in a way that revolutionizes a player's mindset to successfully negotiate the pressures of competitive match play.</p>
    </div>
    <div class="rule"></div>
    <h3 class="author-name">MILES RENFORD</h3>
    <div class="author">
      <div class="author-photo outdoor" role="img" aria-label="Portrait photo of Miles Renford outdoors"></div>
      <p>Miles Renford is a writer and tennis coach. He is a Co-Founder at The Craft of Rally Mastery and has been working to create a theoretical framework for tennis players of all levels to improve. Miles studies the forces that act on the player during a tennis match (both internal and external) and works with players to meet the challenge these forces represent. He runs online and on court programs designed specifically to improve a player's match-day thinking.</p>
    </div>
    <div class="app-mark"><span class="dot"></span>Racket GridDrill</div>
    <div class="code-box"></div>
  </section>

  <section class="spine">
    <div class="spine-text"><span class="thin">THE CRAFT OF </span><span class="bold-light">RALLY </span><span class="bold-dark">MASTERY</span></div>
    <div class="spine-dot"></div>
    <div class="spine-authors">CORWIN HALLOWAY &amp; MILES RENFORD</div>
  </section>

  <section class="front">
    <h1 class="title">
      <span class="line-thin">THE CRAFT OF</span>
      <span class="line-light">RALLY</span>
      <span class="line-dark">MASTERY</span>
    </h1>
    <div class="brand-mark"><span class="dot"></span>CRAFT OF RALLY</div>
    <p class="subtitle">Building a Tactical Edge through Smarter Match Insight</p>
    <p class="byline">CORWIN HALLOWAY &amp; MILES RENFORD</p>
  </section>
</main>
</body>
</html>
```